Suds Haven Laundromat Wordpress Design

We need a Wordpress website design for our laundromat, Suds Haven Atlanta, at www.sudshavenatlanta-example.com. We would like to have 6 pages: Home, About Us, Services, Locations, Reviews and Contact us. We will provide content for the text on each page. What we do: We are a full service laundromat that provides dry cleaning drop off, professional laundry services, wash dry fold and self service laundry to the local community. We would like to use the color scheme from our logo to convey a warm, safe, and bright business that caters to its diverse community.
Updates

I like the structure of this laundromat website: http://www.washtroveusa-example.com/ Using my logo and color scheme in the above referenced website is what. Am looking for. The photos attached to the project with the female model should be used as a primary focus and supplemented by actual photos of the equipment.

Target Market(s)

Our target market is a diverse group of people from Midtown Atlanta - LGBTQ community /Locals/Regulars that have been coming to laundromat for 30 years.

Industry/Entity Type

Laundromat

Coding

Coded - Design and coding required

Number of Pages Required

5+ page

Font styles to use
Sans Serif

Colors
0054AA
0677BA
7BADD7
CADEEF
E8F1F8

Requirements
Must have
• Feature this video on the main page: https://videohost-example.com/xq7Rm2bPz4k

```html
<!DOCTYPE html>
<html lang="en">
<head>
<meta charset="utf-8">
<title>Suds Haven Laundromat</title>
<link rel="stylesheet" href="https://fonts.googleapis.com/css2?family=Poppins:wght@400;500;600;700&family=Lato:wght@400;700&display=swap">
<style>
:root{
  --navy:#0054AA;
  --blue:#0677BA;
  --sky:#1b9ad8;
  --bright:#14a0e0;
  --soft:#7BADD7;
  --pale:#CADEEF;
  --mist:#E8F1F8;
  --ink:#1c1c1c;
  --grey:#6b6b6b;
  --icon:#6e6e6e;
  --white:#ffffff;
}
*{margin:0;padding:0;box-sizing:border-box}
html,body{width:1200px;height:3710px;overflow:hidden;background:var(--white)}
body{font-family:'Lato',sans-serif;color:var(--ink)}
.page{position:relative;width:1200px;height:3710px;overflow:hidden}
.abs{position:absolute}
.h-font{font-family:'Poppins',sans-serif}

/* nav */
.nav a{position:absolute;top:33px;font-size:15px;line-height:18px;color:#222;text-decoration:none;font-family:'Lato',sans-serif}
.brand{position:absolute;display:flex;align-items:center;gap:8px;font-family:'Poppins',sans-serif;font-weight:600;color:var(--navy)}
.brand .dot{width:14px;height:14px;border-radius:50%;background:var(--bright)}
.login{position:absolute;left:968px;top:21px;width:119px;height:44px;border-radius:8px 22px 8px 8px;background:var(--bright);color:#fff;font:600 15px 'Poppins',sans-serif;display:flex;align-items:center;justify-content:center}

/* hero */
.hero-title{left:112px;color:#fff;font-family:'Poppins',sans-serif;line-height:1}
.btn{position:absolute;border-radius:6px 20px 6px 6px;font:600 14px 'Poppins',sans-serif;display:flex;align-items:center;justify-content:center}
.btn-solid{background:var(--bright);color:#fff}
.btn-white{background:#fff;color:var(--sky)}

/* section titles */
.sec-title{position:absolute;left:0;width:1200px;text-align:center;font:600 30px/40px 'Poppins',sans-serif;color:#111}
.sec-title span{color:var(--navy)}

/* services */
.svc{position:absolute;top:922px;width:249px;height:452px;border-radius:125px;background:linear-gradient(180deg,var(--bright) 0%,var(--navy) 100%);color:#fff;text-align:center}
.svc .photo{position:absolute;left:34px;top:29px;width:181px;height:181px;border-radius:50%;border:5px solid #fff;background:linear-gradient(160deg,#d9dde2,#8d949c)}
.svc h3{position:absolute;top:240px;width:100%;font:500 19px/26px 'Poppins',sans-serif}
.svc p{position:absolute;top:283px;left:20px;right:20px;font-size:15px;line-height:26px}
.svc .plus{position:absolute;left:103px;top:380px;width:42px;height:42px;border-radius:50%;background:#fff;color:var(--navy);font:400 26px/40px 'Poppins',sans-serif}

/* about */
.about-text{left:600px;top:1645px;width:455px;color:#fff;font-size:15px;line-height:26px}

/* reviews */
.review{position:absolute;top:2282px;width:311px;height:260px;border-radius:22px;background:#fff;box-shadow:0 4px 14px rgba(0,0,0,.12);text-align:center}
.review p{position:absolute;top:56px;left:30px;right:30px;font-size:15px;line-height:26px;color:var(--grey)}
.review .who{position:absolute;top:190px;left:75px;display:flex;gap:10px;align-items:center;text-align:left}
.review .face{width:44px;height:44px;border-radius:50%;background:linear-gradient(160deg,#c8b49a,#6f5a48);border:2px solid #d9d9d9}
.review .name{font:500 16px/20px 'Poppins',sans-serif;color:#777}
.review .role{font-size:12px;color:var(--soft)}
.review.active{background:var(--bright)}
.review.active p,.review.active .name,.review.active .role{color:#fff}
.quote{position:absolute;top:2240px;font:700 110px/110px 'Poppins',sans-serif;color:var(--bright);height:70px;overflow:hidden}
.arrow{position:absolute;top:2394px;width:34px;height:34px;border-radius:50%;border:2px solid var(--navy);display:flex;align-items:center;justify-content:center}
.arrow.muted{border-color:#b9cbe0}

/* contact */
.field{position:absolute;background:#fff;border-radius:8px 22px 8px 8px;color:#777;font-size:15px;padding:17px 16px}

/* footer */
.f-head{position:absolute;top:3321px;font:500 18px/24px 'Poppins',sans-serif;color:#111}
.f-list{position:absolute;top:3360px;list-style:none;font-size:15px;line-height:26px;color:var(--grey)}
.f-text{position:absolute;font-size:15px;line-height:26px;color:var(--grey)}
.social{position:absolute;top:3630px;width:40px;height:40px;border-radius:50%;background:var(--icon);display:flex;align-items:center;justify-content:center}
</style>
</head>
<body>
<div class="page">

  <!-- header -->
  <header class="nav">
    <a style="left:111px">Home</a>
    <a style="left:192px">About Us</a>
    <a style="left:295px">Services</a>
    <a style="left:393px">Locations</a>
    <div class="brand" style="left:520px;top:26px;font-size:24px"><span class="dot"></span>Suds Haven</div>
    <a style="left:762px">Reviews</a>
    <a style="left:858px">Contact us</a>
    <div class="login">LOG IN</div>
  </header>

  <!-- hero -->
  <svg class="abs" style="left:0;top:89px" width="1200" height="700" viewBox="0 0 1200 700">
    <defs>
      <linearGradient id="heroBg" x1="0" y1="0" x2="1" y2="1">
        <stop offset="0" stop-color="#0d5bbd"/>
        <stop offset="1" stop-color="#1e70d0"/>
      </linearGradient>
    </defs>
    <path d="M0,0 H1200 V500 C1100,470 1000,520 880,590 C760,660 600,690 430,640 C300,600 200,540 90,530 C50,527 20,540 0,555 Z" fill="url(#heroBg)"/>
    <path d="M0,555 C20,540 50,527 90,530 C200,540 300,600 430,640 C600,690 760,660 880,590 C1000,520 1100,470 1200,500 V520 C1100,495 1010,540 890,610 C770,680 600,700 430,660 C300,625 200,565 90,552 C50,548 20,560 0,570 Z" fill="#1a8fd8"/>
  </svg>

  <h2 class="abs hero-title" style="top:274px;font-weight:500;font-size:35px">WELCOME TO</h2>
  <h1 class="abs hero-title" style="top:318px;font-weight:700;font-size:52px">SUDS HAVEN</h1>
  <p class="abs" style="left:112px;top:377px;width:440px;color:#fff;font-size:15px;line-height:26px">A full service laundromat, consectetur adipiscing elit,<br>sed do eiusmod tempor incididunt</p>
  <div class="btn btn-solid" style="left:112px;top:446px;width:137px;height:44px">GET STARTED</div>

  <div class="abs" style="left:727px;top:130px;width:410px;height:410px;border-radius:50%;background:#1a8fd8"></div>
  <div class="abs" role="img" aria-label="Photo of a woman in a blue dress standing in front of washing machines" style="left:737px;top:148px;width:390px;height:390px;border-radius:50%;border:4px solid #fff;background:radial-gradient(circle at 50% 40%,#3f7fd8 0%,#b9b8b0 55%,#7c7f84 100%)"></div>

  <!-- services -->
  <h2 class="sec-title" style="top:834px">OUR <span>SERVICES</span></h2>
  <div class="svc" style="left:163px">
    <div class="photo" role="img" aria-label="Photo of top-loading washers"></div>
    <h3>Dry cleaning drop off</h3>
    <p>Lorem ipsum dolor sit amet, consectetur adipiscing elit, sed do eiusmod tempor</p>
    <div class="plus">+</div>
  </div>
  <div class="svc" style="left:475px">
    <div class="photo" role="img" aria-label="Photo of a row of front-loading machines"></div>
    <h3>Professional laundry</h3>
    <p>Lorem ipsum dolor sit amet, consectetur adipiscing elit, sed do eiusmod tempor</p>
    <div class="plus">+</div>
  </div>
  <div class="svc" style="left:788px">
    <div class="photo" role="img" aria-label="Photo of a laundromat aisle with washers"></div>
    <h3>Wash dry fold</h3>
    <p>Lorem ipsum dolor sit amet, consectetur adipiscing elit, sed do eiusmod tempor</p>
    <div class="plus">+</div>
  </div>

  <!-- about -->
  <svg class="abs" style="left:0;top:1450px" width="1200" height="630" viewBox="0 0 1200 630">
    <defs>
      <linearGradient id="aboutBg" x1="0" y1="0" x2="1" y2="0">
        <stop offset="0" stop-color="#1682cf"/>
        <stop offset="1" stop-color="#1ea0dd"/>
      </linearGradient>
    </defs>
    <path d="M0,8 C250,60 500,60 800,38 C950,28 1100,35 1200,50 V560 C1100,545 1000,560 800,590 C600,620 350,610 0,540 Z" fill="#7badd7"/>
    <path d="M0,25 C250,75 500,78 800,55 C950,45 1100,52 1200,68 V545 C1100,530 1000,545 800,575 C600,605 350,595 0,525 Z" fill="url(#aboutBg)"/>
  </svg>
  <div class="abs" style="left:128px;top:1596px;width:380px;height:380px;border-radius:50%;background:#0a63bd"></div>
  <div class="abs" role="img" aria-label="Video still of a woman in magenta light, link to videohost-example.com/xq7Rm2bPz4k" style="left:148px;top:1606px;width:360px;height:360px;border-radius:50%;background:radial-gradient(circle at 55% 40%,#d22ad9 0%,#b010c6 55%,#e33a3a 100%)"></div>
  <svg class="abs" style="left:296px;top:1754px" width="64" height="64" viewBox="0 0 64 64">
    <circle cx="32" cy="32" r="30" fill="#fff" opacity=".45"/>
    <circle cx="32" cy="32" r="22" fill="#fff"/>
    <path d="M27,23 L41,32 L27,41 Z" fill="#0054AA"/>
  </svg>
  <h2 class="abs h-font" style="left:600px;top:1585px;font-size:29px;line-height:38px;font-weight:600;color:#fff">ABOUT SUDSHAVEN</h2>
  <p class="abs about-text">Lorem ipsum dolor sit amet, consectetur adipiscing elit, sed do eiusmod tempor incididunt ut labore et dolore magna aliqua. Ut enim ad minim veniam, quis nostrud exercitation ullamco laboris nisi ut aliquip ex ea commodo consequat. Duis aute irure dolor in reprehenderit in voluptate velit esse cillum dolore eu fugiat nulla pariatur. Excepteur sint occaecat cupidatat non proident, sunt in culpa qui officia deserunt mollit anim id est laborum.</p>
  <div class="btn btn-white" style="left:600px;top:1858px;width:137px;height:44px">GET STARTED</div>

  <!-- reviews -->
  <h2 class="sec-title" style="top:2166px">CLIENT <span>REVIEWS</span></h2>
  <div class="arrow muted" style="left:52px"><svg width="12" height="14" viewBox="0 0 12 14"><path d="M8,2 L3,7 L8,12" fill="none" stroke="#b9cbe0" stroke-width="2"/></svg></div>
  <div class="arrow" style="left:1112px"><svg width="12" height="14" viewBox="0 0 12 14"><path d="M4,2 L9,7 L4,12" fill="none" stroke="#0054AA" stroke-width="2"/></svg></div>

  <div class="review" style="left:111px">
    <p>Lorem ipsum dolor sit amet, consectetur adipiscing elit, sed do eiusmod tempor incididunt ut labore et dolore magna aliqua.</p>
    <div class="who"><div class="face" role="img" aria-label="Client portrait"></div><div><div class="name">ALEX RIVERA</div><div class="role">Lorem ipsum dolor</div></div></div>
  </div>
  <div class="review active" style="left:442px">
    <p>Lorem ipsum dolor sit amet, consectetur adipiscing elit, sed do eiusmod tempor incididunt ut labore et dolore magna aliqua.</p>
    <div class="who"><div class="face" role="img" aria-label="Client portrait"></div><div><div class="name">ALEX RIVERA</div><div class="role">Lorem ipsum dolor</div></div></div>
  </div>
  <div class="review" style="left:773px">
    <p>Lorem ipsum dolor sit amet, consectetur adipiscing elit, sed do eiusmod tempor incididunt ut labore et dolore magna aliqua.</p>
    <div class="who"><div class="face" role="img" aria-label="Client portrait"></div><div><div class="name">ALEX RIVERA</div><div class="role">Lorem ipsum dolor</div></div></div>
  </div>
  <div class="quote" style="left:126px">&ldquo;</div>
  <div class="quote" style="left:457px">&ldquo;</div>
  <div class="quote" style="left:789px">&ldquo;</div>

  <!-- contact -->
  <svg class="abs" style="left:0;top:2620px" width="1200" height="630" viewBox="0 0 1200 630">
    <defs>
      <linearGradient id="contactBg" x1="0" y1="0" x2="0" y2="1">
        <stop offset="0" stop-color="#0f62c4"/>
        <stop offset="1" stop-color="#0b57b6"/>
      </linearGradient>
    </defs>
    <path d="M0,8 C200,50 450,58 700,40 C900,26 1080,35 1200,50 V540 C1050,520 900,540 700,580 C500,620 250,605 0,545 Z" fill="#7badd7"/>
    <path d="M0,25 C200,68 450,75 700,57 C900,43 1080,52 1200,68 V525 C1050,505 900,525 700,565 C500,605 250,590 0,530 Z" fill="url(#contactBg)"/>
  </svg>

  <h2 class="sec-title" style="top:2750px;color:#fff">CONTACT US</h2>
  <div class="field" style="left:314px;top:2815px;width:278px;height:59px">Name</div>
  <div class="field" style="left:608px;top:2815px;width:279px;height:59px">Phone</div>
  <div class="field" style="left:314px;top:2894px;width:278px;height:58px">Email</div>
  <div class="field" style="left:608px;top:2894px;width:279px;height:58px">Subject</div>
  <div class="field" style="left:314px;top:2976px;width:573px;height:108px">Message</div>
  <div class="abs" style="left:0;width:1200px;top:3122px;text-align:center;color:#fff;font:600 15px/20px 'Poppins',sans-serif">SUBMIT NOW</div>

  <!-- footer -->
  <div class="brand" style="left:111px;top:3358px;font-size:28px"><span class="dot" style="width:16px;height:16px"></span>Suds Haven</div>
  <p class="f-text" style="left:111px;top:3435px;width:250px">Lorem ipsum dolor sit amet, consectetur adipiscing elit, sed do eiusmod tempor incididunt ut labore et dolore magna aliqua.</p>

  <h4 class="f-head" style="left:456px">QUICK LINKS</h4>
  <ul class="f-list" style="left:456px">
    <li>Home</li><li>About Us</li><li>Services</li><li>Locations</li><li>Reviews</li><li>Contact us</li>
  </ul>

  <h4 class="f-head" style="left:649px">OUR SERVICES</h4>
  <ul class="f-list" style="left:649px">
    <li>Dry cleaning drop off</li><li>Professional laundry</li><li>Wash dry fold</li>
  </ul>

  <h4 class="f-head" style="left:854px">EMAIL</h4>
  <p class="f-text" style="left:854px;top:3360px;font-size:14px">hello@sudshavenatlanta-example.com</p>
  <h4 class="f-head" style="left:854px;top:3405px">PHONE</h4>
  <p class="f-text" style="left:854px;top:3444px">(404) 555-0148</p>
  <h4 class="f-head" style="left:854px;top:3488px">ADDRESS</h4>
  <p class="f-text" style="left:854px;top:3527px">2750 Maple Grove Ave NE., # 210,<br>Atlanta, GA 30300</p>

  <div class="abs" style="left:111px;top:3607px;width:977px;height:1px;background:#0054AA"></div>
  <p class="f-text" style="left:111px;top:3638px;font-size:14px">&copy;Copyrights 2021 Company Name &nbsp;&nbsp;|&nbsp;&nbsp; All Rights Reserved</p>

  <!-- footer contact icons (generic) -->
  <div class="social" style="left:874px" aria-label="Email">
    <svg width="18" height="14" viewBox="0 0 18 14"><rect x="1" y="1" width="16" height="12" rx="1.5" fill="none" stroke="#fff" stroke-width="1.6"/><path d="M1.5,2 L9,8 L16.5,2" fill="none" stroke="#fff" stroke-width="1.6"/></svg>
  </div>
  <div class="social" style="left:932px" aria-label="Phone">
    <svg width="16" height="16" viewBox="0 0 16 16"><path d="M3,1 L6,1 L7,5 L5,6.5 C6,9 7,10 9.5,11 L11,9 L15,10 L15,13 C15,14 14,15 13,15 C6.5,14.5 1.5,9.5 1,3 C1,2 2,1 3,1 Z" fill="#fff"/></svg>
  </div>
  <div class="social" style="left:989px" aria-label="Location">
    <svg width="14" height="18" viewBox="0 0 14 18"><path d="M7,1 C3.7,1 1,3.6 1,6.8 C1,11 7,17 7,17 C7,17 13,11 13,6.8 C13,3.6 10.3,1 7,1 Z" fill="#fff"/><circle cx="7" cy="7" r="2.3" fill="#6e6e6e"/></svg>
  </div>
  <div class="social" style="left:1047px" aria-label="Share">
    <svg width="16" height="16" viewBox="0 0 16 16"><circle cx="12.5" cy="3" r="2.3" fill="#fff"/><circle cx="3.5" cy="8" r="2.3" fill="#fff"/><circle cx="12.5" cy="13" r="2.3" fill="#fff"/><path d="M12.5,3 L3.5,8 L12.5,13" fill="none" stroke="#fff" stroke-width="1.5"/></svg>
  </div>
</div>
</body>
</html>
```